Exciting opportunity to create logo and a label for our natural health brand.

About us

We are a customer centric health supplement brand who believes in natural medicine and high quality ingredients. We take a holistic approach to healthcare, with an eastern philosophy. We believe in being partners with our customers in their health care journey and are invested in their well being.

Our brand philosophy and values are attached (see Vorna philosophy.png). Our personality traits are:

- Natural
- Fresh
- Modern
- Balanced (in a holistic sense)

Task breakdown

1. Design a fresh feeling logo for us
- We want it to represent our values and high quality ingredients. We would like the quality of the product to be reflected in the branding and have a high end feel.
- Logo text must include Vorna Health Sciences
- We want the Vorna to be the focus of the logo (see uploaded image Vorna logo example.png)
The logo does not have to follow this layout, but we just want the Vorna to stand out. Feel free to use your creative license on this!

2. Create an attractive label to go on the supplement bottle
- The designs need to be eye catching, give a sense of high end ingredients and natural products and tie in with the logo to give a joined up feel.
- We are selling our products online and need them to really stand out from the competition.
- See examples of labels and packaging we like (1 -7 label design).

The initial label we would like you to design would be for our product Calm Drift. It is a product that assists in the management of Anxiety and stress. The label will appear on the bottle that holds the capsules for this supplement, see uploaded files (Example plain bottles.png). The bottles may be white as the picture shows or dark blue recyclable plastic or dark brown glass . We don't have the exact dimensions of the bottle yet, but I will follow up with these.

The label needs to include the following things:
1. The logo
2. The name of the product
3. The product is to help with the relief of Anxiety and Stress
4. Number of capsules the bottle contains
5. The back of the label should have
i) The ingredients
ii) Dosage
iii) Directions of use

Please use placeholder text where needed.

We look forward to seeing your design. Thank you.

```html
<!DOCTYPE html>
<html lang="en">
<head>
<meta charset="utf-8">
<title>Vorna Health Sciences – Calm Drift label range</title>
<link rel="stylesheet" href="https://fonts.googleapis.com/css2?family=Bebas+Neue&family=Playfair+Display:ital@1&family=Poppins:wght@300;400;600&display=swap">
<style>
  :root {
    --page: #ffffff;
    --label-light: #f6f3ea;
    --label-dark: #e4dfd0;
    --ink: #3a3a38;
    --ink-soft: #4a4a48;
    --gold: #d9a94a;
    --mauve: #b8a1ad;
    --blue: #5f8098;
    --teal: #4e8987;
    --leaf-tone: #d8d3c6;
  }
  * { margin: 0; padding: 0; box-sizing: border-box; }
  html, body {
    width: 1200px; height: 718px; overflow: hidden;
    background: var(--page);
  }
  .range { position: relative; width: 1200px; height: 718px; }
  .label {
    position: absolute; top: 241px; width: 251px; height: 295px;
    background: linear-gradient(90deg, var(--label-dark) 0%, var(--label-light) 45%, var(--label-light) 70%, var(--label-dark) 100%);
    font-family: "Poppins", sans-serif;
    color: var(--ink);
    overflow: hidden;
  }
  .label--gold  { left: 37px;  --accent: var(--gold); }
  .label--mauve { left: 329px; --accent: var(--mauve); }
  .label--blue  { left: 621px; --accent: var(--blue); }
  .label--teal  { left: 913px; --accent: var(--teal); }

  .brand {
    position: absolute; left: 45px; top: 38px;
    display: flex; align-items: center; gap: 7px;
  }
  .brand__dot {
    width: 8px; height: 8px; border-radius: 50%;
    background: var(--ink);
  }
  .brand__name {
    font-family: "Poppins", sans-serif; font-weight: 400;
    font-size: 9.5px; letter-spacing: 1.6px; color: var(--ink);
    text-transform: uppercase; white-space: nowrap;
  }
  .botanical {
    position: absolute; left: 150px; top: 16px; width: 92px; height: 110px;
    border-radius: 46px 46px 40px 40px;
    background: radial-gradient(ellipse at 55% 45%, var(--leaf-tone) 0%, rgba(216,211,198,0) 72%);
  }
  .product-name {
    position: absolute; left: 43px; top: 154px;
    font-family: "Bebas Neue", sans-serif; font-weight: 400; font-size: 42px; line-height: 1;
    letter-spacing: 0.6px; color: var(--ink);
  }
  .ingredients-band {
    position: absolute; left: 41px; top: 203px; width: 166px; height: 22px;
    background: linear-gradient(90deg, transparent 0%, var(--accent) 30%, var(--accent) 62%, transparent 100%);
    opacity: 0.8;
  }
  .ingredients {
    position: absolute; left: 45px; top: 204px;
    font-family: "Playfair Display", serif; font-style: italic;
    font-size: 13px; line-height: 20px; color: var(--ink-soft); white-space: nowrap;
  }
  .benefit {
    position: absolute; left: 45px; top: 233px;
    font-size: 10.5px; letter-spacing: 1.4px; line-height: 16px; color: var(--ink);
    font-weight: 300;
  }
  .benefit strong { font-weight: 600; }
  .benefit span { font-weight: 400; }
  .footer-band {
    position: absolute; left: 0; top: 270px; width: 100%; height: 17px;
    background: var(--accent);
    opacity: 0.8;
    font-size: 7.8px; letter-spacing: 1.1px; line-height: 17px;
    padding-left: 45px; color: var(--ink); white-space: nowrap;
  }
  .label--blue .footer-band, .label--teal .footer-band { color: #f2f2ee; }
</style>
</head>
<body>
<main class="range">
  <section class="label label--gold">
    <div class="brand"><span class="brand__dot"></span><span class="brand__name">Vorna Health Sciences</span></div>
    <div class="botanical" role="img" aria-label="Fine line botanical drawing of a leafy sprig"></div>
    <h1 class="product-name">CALM DRIFT</h1>
    <div class="ingredients-band"></div>
    <p class="ingredients">Vitamins · Minerals · Herbs</p>
    <p class="benefit">RELIEF OF<br><strong>ANXIETY</strong> <span>AND</span> <strong>STRESS</strong></p>
    <div class="footer-band">60 CAPSULES | DIETARY SUPPLEMENT</div>
  </section>
  <section class="label label--mauve">
    <div class="brand"><span class="brand__dot"></span><span class="brand__name">Vorna Health Sciences</span></div>
    <div class="botanical" role="img" aria-label="Fine line botanical drawing of a leafy sprig"></div>
    <h1 class="product-name">CALM DRIFT</h1>
    <div class="ingredients-band"></div>
    <p class="ingredients">Vitamins · Minerals · Herbs</p>
    <p class="benefit">RELIEF OF<br><strong>ANXIETY</strong> <span>AND</span> <strong>STRESS</strong></p>
    <div class="footer-band">60 CAPSULES | DIETARY SUPPLEMENT</div>
  </section>
  <section class="label label--blue">
    <div class="brand"><span class="brand__dot"></span><span class="brand__name">Vorna Health Sciences</span></div>
    <div class="botanical" role="img" aria-label="Fine line botanical drawing of a leafy sprig"></div>
    <h1 class="product-name">CALM DRIFT</h1>
    <div class="ingredients-band"></div>
    <p class="ingredients">Vitamins · Minerals · Herbs</p>
    <p class="benefit">RELIEF OF<br><strong>ANXIETY</strong> <span>AND</span> <strong>STRESS</strong></p>
    <div class="footer-band">60 CAPSULES | DIETARY SUPPLEMENT</div>
  </section>
  <section class="label label--teal">
    <div class="brand"><span class="brand__dot"></span><span class="brand__name">Vorna Health Sciences</span></div>
    <div class="botanical" role="img" aria-label="Fine line botanical drawing of a leafy sprig"></div>
    <h1 class="product-name">CALM DRIFT</h1>
    <div class="ingredients-band"></div>
    <p class="ingredients">Vitamins · Minerals · Herbs</p>
    <p class="benefit">RELIEF OF<br><strong>ANXIETY</strong> <span>AND</span> <strong>STRESS</strong></p>
    <div class="footer-band">60 CAPSULES | DIETARY SUPPLEMENT</div>
  </section>
</main>
</body>
</html>
```